Local fast-growing company in the service sector

We are looking for a modern business card design, which should also appear on our letterheads

Target Market(s)

Private and industrial sectors

Contact Information for Business Card

Vorname Name
Kellberger Str. 18
72486 Lindenbach
Tel.: 07146-839214-0
Name@agentur-kvtl.de

Colors
9d9d9d
919191
aaaaaa

Requirements
Must have
• The logo (file) in silver

```html
<!DOCTYPE html>
<html lang="de">
<head>
<meta charset="utf-8">
<title>KVTL Visitenkarte</title>
<link rel="stylesheet" href="https://fonts.googleapis.com/css2?family=Open+Sans:wght@400;600;700&display=swap">
<style>
  :root {
    --stage: #000000;
    --card-front: #f2f2f2;
    --ink: #1a1a1a;
    --silver: #9d9d9d;
    --silver-mid: #aaaaaa;
    --silver-dark: #919191;
    --white: #ffffff;
  }
  * { margin: 0; padding: 0; box-sizing: border-box; }
  html, body {
    width: 1200px; height: 900px; overflow: hidden;
    background: var(--stage);
    font-family: "Open Sans", Arial, sans-serif;
  }
  .canvas { position: relative; width: 1200px; height: 900px; }

  .card-front {
    position: absolute; left: 265px; top: 200px;
    width: 310px; height: 502px;
    background: var(--card-front);
    border-radius: 52px 0 52px 0;
    color: var(--ink);
  }
  .brand {
    position: absolute; left: 26px; top: 118px;
    display: flex; align-items: center; gap: 14px;
  }
  .brand-mark {
    width: 40px; height: 40px; background: var(--silver);
  }
  .brand-name {
    font-size: 56px; font-weight: 700; letter-spacing: 2px;
    color: var(--silver); line-height: 1;
  }
  .contact { position: absolute; left: 27px; top: 330px; }
  .contact-name {
    font-size: 16.5px; font-weight: 600; letter-spacing: 0.2px;
    line-height: 22px;
    margin-bottom: 10px;
  }
  .contact-address { font-size: 13.5px; line-height: 18px; margin-bottom: 10px; }
  .contact-list { list-style: none; font-size: 13.5px; line-height: 18px; }
  .contact-list li { display: flex; align-items: center; gap: 6px; }
  .contact-list svg { width: 12px; height: 12px; fill: var(--ink); flex: none; }

  .card-back {
    position: absolute; left: 641px; top: 200px;
    width: 309px; height: 502px;
    border-radius: 0 52px 0 52px;
    background: linear-gradient(135deg, #6e6e6e 0%, var(--silver-dark) 25%, #c9c9c9 50%, var(--silver-mid) 68%, #6a6a6a 100%);
    display: flex; align-items: center; justify-content: center; gap: 12px;
  }
  .back-mark {
    width: 34px; height: 34px; background: var(--white);
  }
  .back-name {
    font-size: 52px; font-weight: 700; letter-spacing: 2px;
    color: var(--white); line-height: 1;
  }
</style>
</head>
<body>
<main class="canvas">
  <section class="card-front">
    <div class="brand">
      <span class="brand-mark"></span>
      <span class="brand-name">KVTL</span>
    </div>
    <div class="contact">
      <p class="contact-name">VORNAME NAME</p>
      <p class="contact-address">Kellberger Str. 18<br>72486 Lindenbach</p>
      <ul class="contact-list">
        <li>
          <svg viewBox="0 0 24 24" aria-hidden="true"><path d="M6.6 10.8a15.1 15.1 0 0 0 6.6 6.6l2.2-2.2a1 1 0 0 1 1-.25 11.4 11.4 0 0 0 3.6.57 1 1 0 0 1 1 1V20a1 1 0 0 1-1 1A17 17 0 0 1 3 4a1 1 0 0 1 1-1h3.5a1 1 0 0 1 1 1c0 1.25.2 2.45.57 3.6a1 1 0 0 1-.25 1z"/></svg>
          07146-839214-0
        </li>
        <li>
          <svg viewBox="0 0 24 24" aria-hidden="true"><path d="M2 5h20v14H2z"/><path d="M2 5l10 8 10-8z" fill="#f2f2f2"/></svg>
          Name@agentur-kvtl.de
        </li>
        <li>
          <svg viewBox="0 0 24 24" aria-hidden="true"><circle cx="12" cy="12" r="10"/><path d="M7 8h4v3H8zM13 13h4l-1 4h-3z" fill="#f2f2f2"/></svg>
          www.agentur-kvtl.de
        </li>
      </ul>
    </div>
  </section>

  <section class="card-back">
    <span class="back-mark"></span>
    <span class="back-name">KVTL</span>
  </section>
</main>
</body>
</html>
```